We need a wordpress design that will incorporate a professional color scheme with company logo in a clean layout. The design needs to consider that this will be developed on a responsive theme. Colors are blue and green of the logo and and an accent color (perhaps very light brown/tan). Client wants a 'modern' look.

Industry/Entity Type

It Company

Font styles to use
Serif
Sans Serif

Colors

Designer to choose colors to be used in the design.

Requirements
Must have
• navigation: 1) Home; 2) Services; 3) Auctions by Type; 4) About Us; 5) QVT Bulletin 6) Videos; 7) Contact Us

VERY general idea of layout is attached, Site will have slideshow, image is attached. Widgets used to are: 1) Email Contact Form; 2) social media icons, QT Linkora, ViewNest; 3) Featured Auctions; 4) News & Events blog; Featured Video

Footer will have affiliation logos, contact info and perhaps smaller company logo:
Phone: (512) 555-0147 / Mobile: (512) 555-0183 (Miriam)
Email: mdorrance482@mailbox-example.com / holden@parkelldorrance.example
Address: 417 FM 1382N • #B208 • PMB315 • Austin, TX 78791

Nice to have
• Use of a dropdown menu

```html
<!DOCTYPE html>
<html lang="en">
<head>
<meta charset="utf-8">
<title>Parkell-Dorrance Auction Marketing</title>
<link href="https://fonts.googleapis.com/css2?family=Oswald:wght@300;400&family=Arimo:wght@400;700&display=swap" rel="stylesheet">
<style>
:root{
  --blue:#1b5a8f;
  --blue-dark:#154a78;
  --green:#0f7a3f;
  --green-bright:#12853f;
  --bg:#efefed;
  --white:#ffffff;
  --text:#333333;
}
*{box-sizing:border-box;margin:0;padding:0}
html,body{width:922px;height:1200px;overflow:hidden}
body{position:relative;background:var(--bg);font-family:"Arimo",Arial,sans-serif;color:var(--text)}
.abs{position:absolute}
.cond{font-family:"Oswald","Arial Narrow",sans-serif;font-weight:300}

.site-header{left:0;top:0;width:922px;height:94px;background:linear-gradient(#ffffff,#e9e9e9)}
.brand{left:64px;top:8px;width:150px;text-align:center;color:var(--blue)}
.brand-name{font-family:"Oswald",sans-serif;font-weight:400;font-size:20px;line-height:24px}
.brand-sub{font-weight:700;font-size:13px;line-height:15px;margin-top:6px}
.social{display:flex;gap:6px}
.social span{display:block;height:29px;padding:0 5px;line-height:29px;font-size:10px;color:#fff;border-radius:2px;font-weight:700}
.social .b{background:var(--blue)}
.social .g{background:var(--green-bright)}
.head-contact{left:690px;top:46px;font-size:11.5px;color:var(--blue);line-height:24px}
.head-contact div{display:flex;align-items:center;gap:8px}

.main-nav{left:0;top:94px;width:922px;height:32px;background:var(--blue)}
.main-nav ul{list-style:none;display:flex;position:absolute;left:59px;top:0;height:32px}
.main-nav li{color:#fff;font-size:13.5px;line-height:32px;padding:0 22px}
.main-nav li.active{background:var(--green);padding:0 21px}

.hero{left:0;top:126px;width:922px;height:360px;background:linear-gradient(180deg,#8a9b8f 0%,#5f7d6f 45%,#b7b4ae 80%,#8c8883 100%)}
.hero-box{left:138px;top:242px;width:344px;height:164px;background:rgba(27,90,143,.72);border-radius:0 0 4px 0;padding:10px 16px;color:#fff}
.hero-box h1{font-family:"Oswald",sans-serif;font-weight:300;font-size:26px;line-height:32px}
.btn{display:inline-block;border:2px solid #fff;outline:1px solid var(--blue);color:#fff;font-family:"Oswald",sans-serif;font-weight:300;font-size:16px;border-radius:3px;text-align:center}
.btn-blue{background:var(--blue)}
.btn-green{background:var(--green-bright)}
.hero-box .btn{position:absolute;left:111px;top:108px;width:100px;height:31px;line-height:27px}

.promo{left:59px;top:502px;width:803px;height:96px;background:var(--blue);border-radius:3px;overflow:hidden}
.promo-icon{left:0;top:0;width:105px;height:96px;background:var(--green)}
.promo p{left:118px;top:8px;width:500px;color:#fff;font-family:"Oswald",sans-serif;font-weight:300;font-size:19.5px;line-height:24px}
.promo .btn{position:absolute;left:669px;top:34px;width:98px;height:30px;line-height:26px}

.card{background:var(--white);border-radius:4px;overflow:hidden}
.card h2{background:var(--blue);color:#fff;font-family:"Oswald",sans-serif;font-weight:300;font-size:18px;height:48px;display:flex;align-items:center;justify-content:center;text-align:center;line-height:20px}
.card .ph{margin:8px;height:112px}
.card p{font-size:11.5px;line-height:17.6px;padding:8px 13px 6px}

.news{left:69px;top:996px;font-size:19.5px;color:var(--blue)}
.news-btn{left:728px;top:994px;width:118px;height:30px;line-height:26px}

.site-footer{left:0;top:1044px;width:922px;height:156px;background:var(--green);border-top:4px solid var(--blue)}
.f-title{font-family:"Oswald",sans-serif;font-weight:300;font-size:18px;color:#fff}
.f-input{width:200px;height:24px;background:#fff;font-size:10.5px;color:#666;padding:0 7px;line-height:24px}
.f-contact{font-size:9.5px;color:#fff;line-height:17.6px}
.f-contact div{display:flex;align-items:center;gap:6px}
.badge{width:44px;height:40px;background:rgba(255,255,255,.85)}
.copy{left:0;width:922px;top:1181px;text-align:center;font-size:9.5px;color:#fff}
.copy b{text-decoration:underline}
</style>
</head>
<body>

<header class="site-header abs">
  <div class="brand abs">
    <div class="brand-name">Allied Heartland</div>
    <div class="brand-sub">Parkell-Dorrance<br>Auction Marketing</div>
  </div>
  <div class="social abs" style="left:718px;top:7px">
    <span class="b">Linkora</span><span class="g">QT</span><span class="b">ViewNest</span>
  </div>
  <div class="head-contact abs">
    <div><svg width="14" height="14" viewBox="0 0 24 24"><path fill="#1b5a8f" d="M6.6 10.8a15 15 0 0 0 6.6 6.6l2.2-2.2a1 1 0 0 1 1-.25 11 11 0 0 0 3.6.6 1 1 0 0 1 1 1V20a1 1 0 0 1-1 1A17 17 0 0 1 3 4a1 1 0 0 1 1-1h3.5a1 1 0 0 1 1 1 11 11 0 0 0 .6 3.6 1 1 0 0 1-.25 1z"/></svg>mdorrance482@mailbox-example.com</div>
    <div><svg width="14" height="11" viewBox="0 0 24 18"><path fill="#1b5a8f" d="M0 0h24v2L12 10 0 2zM0 4l12 8 12-8v14H0z"/></svg>(512) 555-0183</div>
  </div>
</header>

<nav class="main-nav abs">
  <ul>
    <li class="active">Home</li><li>Services</li><li>Auctions by Type</li><li>About</li><li>QVT Bulletin</li><li>Videos</li><li>Contact</li>
  </ul>
</nav>

<section class="hero abs" role="img" aria-label="Machine shop floor with green industrial lathes and equipment"></section>
<div class="hero-box abs">
  <h1>Lorem Ipsum is simply dummy text of the printing and setting industry. Lorem Ipsum.</h1>
  <span class="btn btn-blue">LEARN MORE</span>
</div>

<section class="promo abs">
  <div class="promo-icon abs">
    <svg class="abs" style="left:23px;top:18px" width="60" height="60" viewBox="0 0 60 60"><circle cx="30" cy="30" r="28" fill="none" stroke="#fff" stroke-width="3"/><circle cx="30" cy="30" r="20" fill="none" stroke="#fff" stroke-width="3"/><circle cx="30" cy="30" r="12" fill="#fff"/></svg>
  </div>
  <p class="abs">The go-to business asset liquidation and real estate-at-auction solution provider in Texas and across the southwest for over 30 years using our proprietary QVT™ process.</p>
  <span class="btn btn-green">LEARN MORE</span>
</section>

<article class="card abs" style="left:59px;top:614px;width:272px;height:362px">
  <h2>Upcoming Actions</h2>
  <p>Lorem Ipsum is simply dummy text of the printing and typesetting industry. Lorem Ipsum has been the industry's standard dummy text ever.</p>
  <div role="img" aria-label="Glass office towers seen from below with tree leaves" style="margin:6px 8px;height:176px;background:linear-gradient(135deg,#4a6b8c,#7fa7d6 50%,#3c4f63)"></div>
  <span class="btn btn-blue abs" style="left:66px;top:321px;width:122px;height:31px;line-height:27px">MORE AUCTIONS</span>
</article>

<article class="card abs" style="left:358px;top:614px;width:240px;height:170px">
  <h2>Real Estate</h2>
  <div class="ph" role="img" aria-label="Single-story white house with dark roof and garden" style="background:linear-gradient(#7fb0e0,#e8eef0 55%,#5f8a3a)"></div>
</article>
<article class="card abs" style="left:622px;top:614px;width:240px;height:170px">
  <h2>Business Liquidations</h2>
  <div class="ph" role="img" aria-label="Business people in suits meeting in a glass office" style="background:linear-gradient(90deg,#9fc2e0,#3d5d7a 50%,#b8d2e8)"></div>
</article>
<article class="card abs" style="left:358px;top:801px;width:240px;height:177px">
  <h2>Commercial, Industrial &amp;<br>Speciality Assets</h2>
  <div class="ph" role="img" aria-label="Retail strip building with red awnings and parking lot" style="background:linear-gradient(#cfd6dc,#8a3b3b 35%,#6a6a66 60%,#b9b9b5)"></div>
</article>
<article class="card abs" style="left:622px;top:801px;width:240px;height:177px">
  <h2>Appraisals</h2>
  <div class="ph" role="img" aria-label="Three professionals reviewing documents at a table" style="background:linear-gradient(90deg,#6b4a30,#d8d4cc 50%,#4a3a30)"></div>
</article>

<div class="news abs">The QVT Bulletin : Holden Parkell Receives Lifetime Achievement Award</div>
<span class="btn btn-green abs news-btn">VIEW ALL NEWS</span>

<footer class="site-footer abs">
  <div class="abs" style="left:69px;top:12px;display:flex;align-items:center;gap:7px">
    <svg width="24" height="18" viewBox="0 0 24 18"><path fill="#fff" d="M0 0h24v2L12 10 0 2zM0 4l12 8 12-8v14H0z"/></svg>
    <span class="f-title">Sign up for Auction Alerts</span>
  </div>
  <div class="f-input abs" style="left:68px;top:42px">Enter your emails</div>
  <div class="f-input abs" style="left:68px;top:74px">Enter your password</div>
  <span class="btn btn-blue abs" style="left:68px;top:106px;width:80px;height:26px;line-height:22px">SIGN UP</span>

  <div class="f-title abs" style="left:336px;top:12px">Contact Info</div>
  <div class="f-contact abs" style="left:338px;top:42px">
    <div><svg width="10" height="13" viewBox="0 0 10 14"><path fill="#fff" d="M5 0a5 5 0 0 1 5 5c0 4-5 9-5 9S0 9 0 5a5 5 0 0 1 5-5zm0 3a2 2 0 1 0 0 4 2 2 0 0 0 0-4z"/></svg>417 FM 1382N • #B208 • PMB315 • Austin, TX 78791</div>
    <div><svg width="10" height="10" viewBox="0 0 24 24"><path fill="#fff" d="M6.6 10.8a15 15 0 0 0 6.6 6.6l2.2-2.2a1 1 0 0 1 1-.25 11 11 0 0 0 3.6.6 1 1 0 0 1 1 1V20a1 1 0 0 1-1 1A17 17 0 0 1 3 4a1 1 0 0 1 1-1h3.5a1 1 0 0 1 1 1 11 11 0 0 0 .6 3.6 1 1 0 0 1-.25 1z"/></svg>Phone: (512) 555-0147</div>
    <div><svg width="10" height="12" viewBox="0 0 10 14"><rect x="1" y="0" width="8" height="14" rx="1.5" fill="#fff"/><rect x="2.5" y="2" width="5" height="8" fill="#0f7a3f"/></svg>Mobile: (512) 555-0183 (Miriam)</div>
    <div><svg width="10" height="8" viewBox="0 0 24 18"><path fill="#fff" d="M0 0h24v2L12 10 0 2zM0 4l12 8 12-8v14H0z"/></svg>Email: mdorrance482@mailbox-example.com</div>
    <div><svg width="10" height="8" viewBox="0 0 24 18"><path fill="#fff" d="M0 0h24v2L12 10 0 2zM0 4l12 8 12-8v14H0z"/></svg>holden@parkelldorrance.example</div>
  </div>

  <div class="f-title abs" style="left:606px;top:12px">Affiliation Logos</div>
  <div class="abs" style="left:611px;top:42px;display:flex;gap:14px">
    <div class="badge" style="border-radius:50%;width:40px"></div><div class="badge"></div><div class="badge"></div><div class="badge" style="width:72px"></div>
  </div>
  <div class="social abs" style="left:682px;top:100px;gap:8px">
    <span class="b" style="border:1px solid #fff">Linkora</span><span class="g" style="border:1px solid #fff">QT</span><span class="b" style="border:1px solid #fff">ViewNest</span>
  </div>
</footer>
<div class="copy abs">© <b>Allied Heartland</b> - 2014. All Rights Reserved.</div>

</body>
</html>
```